U.S. Popcorn company needs business cards

We are a popcorn company that manufactures popcorn and sells it to grocery stores worldwide. Our theme is "Americana" and our logo is U.S. route 66 which is the most famous highway in the U.S.

We would like the design to be simple and to use both sides. On the back side we would like to see just the logo and website. The front would be normal details

Target Market(s)

Wholesalers, grocers and distributors

Industry/Entity Type

Manufacture

Contact Information for Business Card

Business name: Prairie Lantern Popcorn
Phone: +1 555 308 4726
Email: Dale@prairielanternpopcorn.com
website: www.prairielanternpopcorn.com
Tag Line: "Fresh from the Plains"
Name: Dale Whitcombe
Title: Founder/President

Requirements
Must have
• Either this design should be fun or clean and simple. I will let you show me your thougths.
Nice to have
• Anything that ties in the real Hwy Route 66.
• Colors might need to be red, white and blue incorporated.
Should not have
• Not be too busy.

```html
<!DOCTYPE html>
<html lang="en">
<head>
<meta charset="utf-8">
<title>Prairie Lantern Popcorn – Business Cards</title>
<link href="https://fonts.googleapis.com/css2?family=Open+Sans:wght@400;600;700&display=swap" rel="stylesheet">
<style>
  :root {
    --navy: #1c3a8a;
    --navy-deep: #0f2a78;
    --route-red: #d9262e;
    --paper: #f8f8f6;
    --ink-grey: #3b3b3b;
    --backdrop: #e6e4e1;
  }
  * { margin: 0; padding: 0; box-sizing: border-box; }
  html, body {
    width: 1200px; height: 844px; overflow: hidden;
    background: var(--backdrop);
    font-family: "Open Sans", Arial, sans-serif;
  }
  .sheet {
    position: relative; width: 1200px; height: 844px;
    display: flex; align-items: center; justify-content: center; gap: 60px;
  }
  .card {
    position: relative; width: 525px; height: 300px; flex: none;
    box-shadow: 0 6px 18px rgba(0,0,0,0.18);
  }
  .card--front { background: var(--paper); color: var(--navy); }
  .card--back { background: var(--navy-deep); color: #fff; }

  .brand {
    display: flex; align-items: center; gap: 10px;
    font-weight: 700; font-size: 19px; line-height: 1.15;
  }
  .brand__dot {
    width: 16px; height: 16px; border-radius: 50%;
    background: var(--route-red); flex: none;
  }
  .card--front .brand {
    position: absolute; top: 40px; right: 36px; width: 180px;
    color: var(--navy);
  }

  .person { position: absolute; left: 40px; top: 146px; }
  .person__name {
    font-weight: 700; font-size: 17px; letter-spacing: 0.3px;
    text-transform: uppercase; color: var(--navy);
  }
  .person__title { font-size: 12.5px; color: var(--ink-grey); margin-top: 1px; }

  .contact {
    position: absolute; left: 40px; top: 200px; right: 30px;
    font-size: 12.5px; color: var(--ink-grey);
    display: grid; grid-template-columns: auto 1fr; column-gap: 28px; row-gap: 6px;
  }
  .contact__web { font-weight: 700; color: var(--navy); }
  .contact__label { font-weight: 700; color: var(--navy); margin-right: 4px; }

  .tagline {
    position: absolute; left: 40px; bottom: 26px;
    font-weight: 600; font-size: 16px; letter-spacing: 2.4px;
    color: var(--navy); text-transform: uppercase;
  }

  .card--back .brand {
    position: absolute; left: 0; right: 0; top: 100px;
    justify-content: center; color: #fff; font-size: 22px;
  }
  .card--back .brand__dot { background: #fff; }
  .back__web {
    position: absolute; left: 0; right: 0; top: 168px;
    text-align: center; font-size: 12.5px; color: #fff;
  }
</style>
</head>
<body>
  <main class="sheet">
    <section class="card card--front" aria-label="Business card front">
      <div class="brand"><span class="brand__dot"></span><span>Prairie Lantern Popcorn</span></div>
      <div class="person">
        <p class="person__name">Dale Whitcombe</p>
        <p class="person__title">Founder/President</p>
      </div>
      <div class="contact">
        <span class="contact__web">www.prairielanternpopcorn.com</span>
        <span><span class="contact__label">E:</span>Dale@prairielanternpopcorn.com</span>
        <span><span class="contact__label">P:</span>+1 555 308 4726</span>
        <span></span>
      </div>
      <p class="tagline">Fresh from the Plains</p>
    </section>

    <section class="card card--back" aria-label="Business card back">
      <div class="brand"><span class="brand__dot"></span><span>Prairie Lantern Popcorn</span></div>
      <p class="back__web">www.prairielanternpopcorn.com</p>
    </section>
  </main>
</body>
</html>
```